Medical centre needs a business card

We are a medcial centre in Australia, needing a new business card. Our demographic is low working class families. We are going to be renovating our premises to modernise the look and also had a new logo done a few months ago representing quality and community, and now need to update our cards. It needs to be doubled sided, with logo and contact details on the front, and appointment details on the back. . Needs to be modern and simple, easy to read. <br/><br/>Name: Kindle Grove Medical Centre <br/>Address: 512 Parmley Rd (Cnr Parmley Rd & Osgood Creek Rd),<br/>Tindarra Court Shopping Centre, Paralowie, SA 5108<br/>Ph: 08 8461 3072<br/>Tag line: Where your wellbeing comes first<br/>Website: www.kindlegrovemedicalcentre-example.com.au<br/>Online bookings also available<br/><br/>(On the back, to have 3 lines of appointments that can be written in.<br/>Day, date, time)<br/><br/>Your next appointment is on<br/>Can try “M T W Th F Sa Su _________________ at ____________ am/pm” or other combinations <br/>Please advise as soon as possible if unable to attend<br/>Cancellation fees apply if less than 2 hrs notice<br/>Online appointments available (please highlight this option by either by position, colour or font)

Target Market(s)

Lower social economic working class, young families to seniors

Industry/Entity Type

Medical Centre

Contact Information for Business Card

Kindle Grove Medical Centre
512 Parmley Rd (Cnr Parmley Rd & Osgood Creek Drive)
Tindarra Court Shopping Centre
Marrowfield SA 5197
Ph: 08 8461 3072
www.kindlegrovemedicalcentre-example.com.au
Tagline line: where your wellbeing comes first
Back side is for appointments
Your next appointment is with Dr ______________
Day/date/time (Please give 3 lines of appointments)
Please advise as soon as possible if unable to attend
Cancellation fees apply if less than 2 hours notice
Online appointments available
Book online easily and conveniently (please highlight online appointments)

Font styles to use
Serif
Sans Serif

Colors

Designer to choose colors to be used in the design.

Requirements
Must have
• Modern and simple
• Easy to ready
• Induces a wellbeing feeling
• Incorporate our logo colours and feel from logo
• Induces feeling of stability and security
Nice to have
• Attract attention
• Pleasant to look at
• Feeling of innovation
Should not have
• Loud clashing colours
• Overly luxurious feeling
• Overly artistic

```html
<!DOCTYPE html>
<html lang="en">
<head>
<meta charset="utf-8">
<title>Kindle Grove Medical Centre – Business Card</title>
<link rel="stylesheet" href="https://fonts.googleapis.com/css2?family=Oswald:wght@500&family=Roboto:wght@400;500;700&display=swap">
<style>
  :root {
    --brand-blue: #1086c9;
    --brand-blue-dark: #0a6fab;
    --paper: #ffffff;
    --ink-grey: #555b61;
    --rule-grey: #9aa1a8;
    --backdrop: #e4e5e7;
  }
  * { box-sizing: border-box; margin: 0; padding: 0; }
  html, body { width: 1200px; height: 800px; overflow: hidden; }
  body {
    background: var(--backdrop);
    font-family: "Roboto", Arial, sans-serif;
    display: flex;
    align-items: center;
    justify-content: center;
    gap: 40px;
  }
  .card {
    width: 550px;
    height: 314px;
    position: relative;
    box-shadow: 0 6px 18px rgba(0,0,0,.15);
  }

  /* Front */
  .card-front { background: var(--brand-blue); color: var(--paper); }
  .holder {
    position: absolute; left: 34px; top: 96px; width: 170px;
    font-family: "Oswald", "Arial Narrow", sans-serif; font-weight: 500;
    text-transform: uppercase; line-height: 1.1;
  }
  .holder-name { font-size: 28px; letter-spacing: .5px; }
  .holder-role { font-size: 20px; padding-left: 60px; }
  .divider {
    position: absolute; left: 214px; top: 62px; width: 1px; height: 132px;
    background: rgba(255,255,255,.8);
  }
  .contact {
    position: absolute; left: 232px; top: 58px; right: 14px;
    font-size: 12px; line-height: 1.4; font-style: normal;
  }
  .contact p { white-space: nowrap; }
  .contact-org { font-weight: 700; font-size: 13px; }
  .contact-row { display: flex; align-items: center; gap: 6px; }
  .contact-row svg { width: 11px; height: 11px; flex: none; }
  .tagline {
    position: absolute; left: 0; right: 0; bottom: 34px; text-align: center;
    font-weight: 700; font-size: 16px; letter-spacing: 2.4px; text-transform: uppercase;
  }

  /* Back */
  .card-back { background: var(--paper); border-bottom: 5px solid var(--brand-blue); }
  .slots { position: absolute; left: 30px; right: 30px; top: 24px; }
  .slot {
    display: flex; align-items: flex-end; gap: 6px; height: 30px;
    font-size: 12.5px; color: var(--brand-blue); text-transform: uppercase; letter-spacing: .3px;
  }
  .slot .fill { flex: 1; border-bottom: 1px dotted var(--rule-grey); height: 1px; margin-bottom: 3px; }
  .slot .fill.short { flex: 0 0 130px; }
  .notice {
    position: absolute; left: 30px; bottom: 44px; width: 280px;
    font-size: 11.5px; line-height: 1.35; color: var(--ink-grey);
  }
  .book-online {
    position: absolute; left: 30px; bottom: 18px;
    font-weight: 700; font-size: 16px; color: var(--brand-blue); text-transform: uppercase;
  }
  .brand {
    position: absolute; right: 28px; bottom: 40px; width: 170px;
    display: flex; align-items: center; gap: 10px;
  }
  .brand-square { width: 26px; height: 26px; background: var(--brand-blue); flex: none; }
  .brand-name {
    font-weight: 700; font-size: 15px; line-height: 1.15; color: var(--brand-blue);
    text-transform: uppercase;
  }
</style>
</head>
<body>

  <section class="card card-front" aria-label="Business card front">
    <div class="holder">
      <p class="holder-name">Daniel Marsh</p>
      <p class="holder-role">President</p>
    </div>
    <div class="divider"></div>
    <address class="contact">
      <p class="contact-org">Kindle Grove Medical Centre</p>
      <p>512 Parmley Rd</p>
      <p>(Cnr Parmley Rd &amp; Osgood Creek Drive)</p>
      <p>Tindarra Court Shopping Centre</p>
      <p>Marrowfield SA 5197</p>
      <p class="contact-row">
        <svg viewBox="0 0 24 24" aria-hidden="true"><path fill="#fff" d="M6.6 10.8a15 15 0 0 0 6.6 6.6l2.2-2.2c.3-.3.7-.4 1-.2 1.1.4 2.3.6 3.6.6.6 0 1 .4 1 1V20c0 .6-.4 1-1 1A17 17 0 0 1 3 4c0-.6.4-1 1-1h3.5c.6 0 1 .4 1 1 0 1.3.2 2.5.6 3.6.1.3 0 .7-.2 1z"/></svg>
        08 8461 3072
      </p>
      <p class="contact-row">
        <svg viewBox="0 0 24 24" aria-hidden="true"><circle cx="12" cy="12" r="10" fill="#fff"/><path d="M2 12h20M12 2c3 3 3 17 0 20M12 2c-3 3-3 17 0 20" stroke="#1086c9" stroke-width="1.6" fill="none"/></svg>
        www.kindlegrovemedicalcentre-example.com.au
      </p>
    </address>
    <p class="tagline">Where your wellbeing comes first</p>
  </section>

  <section class="card card-back" aria-label="Business card back">
    <div class="slots">
      <div class="slot"><span>Your next appointment is with Dr :</span><span class="fill"></span></div>
      <div class="slot"><span>Date :</span><span class="fill"></span><span>Time :</span><span class="fill short"></span><span>AM/PM</span></div>
      <div class="slot"><span class="fill"></span></div>
      <div class="slot"><span class="fill"></span></div>
      <div class="slot"><span class="fill"></span></div>
    </div>
    <p class="notice">Please advise as soon as possible if unable to attend. Cancellation fees apply if less than 2 hours notice. Online appointments available</p>
    <p class="book-online">Book online easily &amp; conveniently</p>
    <div class="brand">
      <span class="brand-square"></span>
      <span class="brand-name">Kindle Grove Medical Centre</span>
    </div>
  </section>

</body>
</html>
```